New Business Card Design Project

Need a design that will create an impact / strong impression towards our clients for our business. We are in the lighting business and we do lighting retrofits for large commercial to industrial clientele.

Target Market(s)

Lighting Industry

Industry/Entity Type

Business

Font styles to use
Other font styles liked:
• we would like to use the font on our logo, not sure what it is though..

Requirements
Must have
• Our logo.
Nice to have
• We are open to suggestions that have to do with lighting.

```html
<!DOCTYPE html>
<html lang="en">
<head>
<meta charset="utf-8">
<title>Tessmoor Retrofit Co. — Business Card</title>
<link rel="stylesheet" href="https://fonts.googleapis.com/css2?family=Montserrat:wght@600;700&family=Open+Sans:wght@400&display=swap">
<style>
  :root {
    --stage: #2b2b2b;
    --card-white: #ffffff;
    --brand-green: #0b8435;
    --deep-green: #123d12;
    --leaf-green: #5cc15a;
    --rule-green: #1f8a3a;
    --ink-grey: #555555;
    --on-green: #ffffff;
  }
  * { margin: 0; padding: 0; box-sizing: border-box; }
  html, body {
    width: 1200px; height: 960px; overflow: hidden;
    background: var(--stage);
  }
  .canvas { position: relative; width: 1200px; height: 960px; }

  .card { position: absolute; width: 600px; height: 343px; }
  .card-front { left: 314px; top: 113px; background: var(--card-white); }
  .card-back { left: 311px; top: 472px; background: var(--brand-green); }

  .accent-wedge { position: absolute; left: 0; top: 30px; width: 18px; height: 41px; }

  .holder { position: absolute; left: 26px; top: 30px; }
  .holder-name {
    font-family: "Montserrat", sans-serif; font-weight: 700;
    font-size: 20px; line-height: 24px; color: var(--deep-green); letter-spacing: 0.3px;
  }
  .holder-title {
    font-family: "Open Sans", sans-serif; font-size: 16px; line-height: 20px;
    color: var(--rule-green); letter-spacing: 0.5px;
  }

  .address {
    position: absolute; left: 26px; top: 142px;
    font-family: "Open Sans", sans-serif; font-size: 16px; line-height: 19.5px;
    color: var(--ink-grey); font-style: normal; letter-spacing: 0.3px;
  }

  .contacts { position: absolute; left: 26px; top: 215px; list-style: none; }
  .contacts li {
    display: flex; align-items: center; gap: 8px;
    font-family: "Open Sans", sans-serif; font-size: 16px; line-height: 19px;
    color: var(--ink-grey); letter-spacing: 0.3px;
  }
  .contacts svg { width: 14px; height: 14px; fill: var(--deep-green); flex: none; }

  .wordmark {
    position: absolute; font-family: "Montserrat", sans-serif; font-weight: 700;
    letter-spacing: 1px; white-space: nowrap;
  }
  .wordmark-front { right: 29px; top: 156px; font-size: 30px; color: var(--deep-green); }
  .wordmark-back {
    left: 0; right: 0; top: 156px; text-align: center;
    font-size: 44px; color: var(--on-green);
  }

  .base-rule {
    position: absolute; left: 0; top: 306px; width: 600px; height: 1.5px;
    background: var(--rule-green);
  }
  .web-tag {
    position: absolute; left: 328px; top: 294px; width: 243px; height: 26px;
    background: var(--deep-green); color: var(--on-green);
    font-family: "Open Sans", sans-serif; font-size: 15px; line-height: 26px;
    letter-spacing: 2.2px; text-align: center;
  }
  .web-back {
    position: absolute; left: 0; right: 0; top: 280px; text-align: center;
    font-family: "Open Sans", sans-serif; font-size: 15px; letter-spacing: 2px;
    color: var(--on-green);
  }
</style>
</head>
<body>
<main class="canvas">
  <section class="card card-front" aria-label="Card front">
    <svg class="accent-wedge" viewBox="0 0 18 41" aria-hidden="true">
      <polygon points="0,0 3,0 18,41 0,41" fill="var(--leaf-green)"/>
    </svg>
    <div class="holder">
      <p class="holder-name">DANIEL REYES</p>
      <p class="holder-title">CEO/FOUNDER</p>
    </div>
    <address class="address">214 Harbor View Road<br>Fairbanks<br>Alaska 99701</address>
    <ul class="contacts">
      <li><svg viewBox="0 0 14 14"><path d="M1 4c0-2 2-3 6-3s6 1 6 3v1H10V3.5H4V5H1z M3 6h8l1 7H2z M7 8a1.5 1.5 0 1 0 0.01 0z"/></svg>555 210 4831</li>
      <li><svg viewBox="0 0 14 14"><path d="M4 0h6a1 1 0 0 1 1 1v12a1 1 0 0 1-1 1H4a1 1 0 0 1-1-1V1a1 1 0 0 1 1-1zm1 2v8h4V2zm2 9.2a.9.9 0 1 0 .01 0z"/></svg>555 372 9046</li>
      <li><svg viewBox="0 0 14 14"><path d="M3 1h8v3H3z M1 5h12v6h-2v2H3v-2H1z M4 9v3h6V9z"/></svg>555 618 2290</li>
      <li><svg viewBox="0 0 14 14"><path d="M1 3h12v1L7 8 1 4z M1 5.5l6 4 6-4V11H1z"/></svg>hello@tessmoorco.com</li>
    </ul>
    <p class="wordmark wordmark-front">TESSMOOR</p>
    <div class="base-rule"></div>
    <p class="web-tag">www.tessmoorco.com</p>
  </section>

  <section class="card card-back" aria-label="Card back">
    <p class="wordmark wordmark-back">TESSMOOR</p>
    <p class="web-back">www.tessmoorretrofit.com</p>
  </section>
</main>
</body>
</html>
```